NZ First of it's kind solutions directory and marketplace for busy Mums needs a business card design

We need a business card design for our new nationwide business in NZ (long term plans to go global). We provide solutions to the everyday challenges that busy Mums face by connecting them with quality communities and suppliers of carefully selected, relevant products and services. We sell direct via our online marketplace. The final design should communicate our values of inclusivity, quality and smart solutions. Colours should incorporate our logo colour palette of #477077 and #6ba8b2. Our website is at https://www.brightnestmums.example

Target Market(s)

busy Mums, Age 28 – 50, female, income over $100K, location main centres NZ primarily but NZ wide. Is likely juggling work or career with a young family. Probably had hobbies which have fallen by the wayside.
-Wants to succeed in her chosen career without compromising on family life
-to successfully juggle her career without feeling like she is compromising her children
- Is time poor, something always has to give and it’s generally her health (she’ll stay up late, get stressed)
- probably ex corporate or professional career. Has discretional income

Industry/Entity Type

Business

Contact Information for Business Card

Lena Forbisher, Founder, BrightNestMums.example (Strapline Tap; Gather; Sorted), 47 Kowhai Terrace, Ellerslie, Auckland 1051, New Zealand. Mob: 021 483 517 Ph: +64 (0)9 571 4860

Font styles to use
Other font styles liked:
• Raleway, and/or Architects Daughter

Colors
00a990
33b8a4
86cfc6
cfeae6

Requirements
Must have
• the above details, streamline. the logo and colours associated with those logos
Should not have
• foil or metallic colours

```html
<!DOCTYPE html>
<html lang="en">
<head>
<meta charset="utf-8">
<title>BrightNestMums business card</title>
<link rel="stylesheet" href="https://fonts.googleapis.com/css2?family=Raleway:wght@400;500;700;800&display=swap">
<style>
  :root {
    --teal-dark: #477077;
    --teal-light: #6ba8b2;
    --card: #ffffff;
    --ink-grey: #5a5f61;
    --backdrop: #2b2d2f;
  }
  * { box-sizing: border-box; margin: 0; padding: 0; }
  html, body { width: 1200px; height: 880px; overflow: hidden; }
  body {
    background: var(--backdrop);
    font-family: "Raleway", sans-serif;
    display: flex; flex-direction: column; align-items: center; justify-content: center;
    gap: 60px;
  }
  .card {
    position: relative;
    width: 620px; height: 354px;
    background: var(--card);
    border-radius: 22px;
    overflow: hidden;
    box-shadow: 0 10px 30px rgba(0,0,0,.45);
  }
  .brand { display: flex; align-items: center; gap: 12px; }
  .brand-dot {
    width: 40px; height: 40px; border-radius: 50%;
    background: var(--teal-dark); flex: none;
  }
  .brand-name {
    font-weight: 800; color: var(--teal-dark);
    font-size: 42px; letter-spacing: -0.5px; line-height: 1;
    white-space: nowrap;
  }
  /* front */
  .card-front { display: flex; flex-direction: column; align-items: center; justify-content: center; gap: 22px; }
  .card-front .brand-name { font-size: 46px; }
  .web-line {
    font-size: 14px; font-weight: 500; letter-spacing: 2px; color: var(--teal-dark);
  }
  /* back */
  .waves { position: absolute; inset: 0; width: 100%; height: 100%; }
  .card-back .brand { position: absolute; left: 32px; top: 96px; }
  .card-back .brand-dot { width: 34px; height: 34px; }
  .card-back .brand-name { font-size: 32px; }
  .person { position: absolute; right: 34px; top: 26px; text-align: right; }
  .person-name { font-weight: 800; font-size: 18px; color: var(--teal-dark); }
  .person-role { font-size: 14px; color: var(--ink-grey); }
  .contact {
    position: absolute; right: 22px; top: 172px;
    color: #fff; text-align: right; font-size: 12px; line-height: 1.5; font-weight: 500;
    white-space: nowrap;
  }
  .contact-row { display: flex; justify-content: flex-end; align-items: center; gap: 8px; }
  .contact-icon { width: 14px; height: 14px; flex: none; }
  .contact-address { margin-bottom: 6px; }
</style>
</head>
<body>

  <section class="card card-front">
    <div class="brand">
      <span class="brand-dot"></span>
      <span class="brand-name">BrightNestMums</span>
    </div>
    <p class="web-line">www.brightnestmums.example</p>
  </section>

  <section class="card card-back">
    <svg class="waves" viewBox="0 0 620 354" preserveAspectRatio="none" aria-hidden="true">
      <path d="M0 296 C150 288 250 262 310 180 C280 258 160 312 0 320 Z" fill="var(--teal-light)"/>
      <path d="M0 330 C170 324 290 286 330 210 C365 140 430 96 510 74 C450 108 410 150 370 218 C320 300 190 340 0 350 Z" fill="var(--teal-dark)"/>
      <path d="M150 354 C300 340 360 280 400 210 C440 140 500 100 620 92 L620 354 Z" fill="var(--teal-dark)"/>
    </svg>

    <div class="person">
      <p class="person-name">Lena Forbisher</p>
      <p class="person-role">Founder</p>
    </div>

    <div class="brand">
      <span class="brand-dot"></span>
      <span class="brand-name">BrightNestMums</span>
    </div>

    <div class="contact">
      <p class="contact-address">47 Kowhai Terrace,<br>Ellerslie, Auckland 1051<br>New Zealand</p>
      <p class="contact-row">021 483 517
        <svg class="contact-icon" viewBox="0 0 16 16"><rect x="4" y="1" width="8" height="14" rx="2" fill="none" stroke="#fff" stroke-width="1.5"/><circle cx="8" cy="12" r="1" fill="#fff"/></svg>
      </p>
      <p class="contact-row">+64 (0)9 571 4860
        <svg class="contact-icon" viewBox="0 0 16 16"><path d="M3 2 L6 2 L7 5 L5 6.5 C6 9 7 10 9.5 11 L11 9 L14 10 L14 13 C14 14 13 14.5 12 14.5 C6 14 2 10 1.5 4 C1.5 3 2 2 3 2 Z" fill="#fff"/></svg>
      </p>
      <p class="contact-row">www.brightnestmums.example
        <svg class="contact-icon" viewBox="0 0 16 16"><circle cx="8" cy="8" r="6.5" fill="none" stroke="#fff" stroke-width="1.3"/><ellipse cx="8" cy="8" rx="2.8" ry="6.5" fill="none" stroke="#fff" stroke-width="1.1"/><line x1="1.5" y1="8" x2="14.5" y2="8" stroke="#fff" stroke-width="1.1"/></svg>
      </p>
    </div>
  </section>

</body>
</html>
```